Need Business Card for our Real Estate Business with Sales Executive's Picture

PANTONE 484 C ( RED)

PANTONE 2766 C ( BLUE

Industry/Entity Type

Real Estate

Contact Information for Business Card

Name, Mobile, email, & picture of Person
Agency Phone, address, Web address

Requirements
Must have
• Our Logo Colours, Agent Picture,

```html
<!DOCTYPE html>
<html lang="en">
<head>
<meta charset="utf-8">
<title>Meridian Real Estate – Business Card</title>
<link rel="stylesheet" href="https://fonts.googleapis.com/css2?family=Open+Sans:wght@400;600;700&display=swap">
<style>
  :root {
    --stage: #3a3a3c;
    --card-black: #1c1c1e;
    --card-charcoal: #252527;
    --brand-blue: #17255f;
    --brand-red: #b5242b;
    --text-white: #ffffff;
    --text-soft: #d9dce6;
    --emboss: #4a4a4d;
    --photo-a: #2d4c9a;
    --photo-b: #1a2a66;
  }
  * { box-sizing: border-box; margin: 0; padding: 0; }
  html, body { width: 799px; height: 1200px; overflow: hidden; }
  body {
    background: var(--stage);
    font-family: "Open Sans", Arial, sans-serif;
    position: relative;
  }
  .card {
    position: absolute;
    left: 80px;
    width: 640px;
    height: 366px;
    border-radius: 4px;
    overflow: hidden;
  }

  /* Back side */
  .card-back { top: 110px; background: var(--card-black); }
  .back-brand {
    position: absolute; left: 0; right: 0; top: 128px;
    text-align: center;
    font-size: 44px; font-weight: 700; letter-spacing: 10px;
    color: var(--emboss);
  }
  .back-web {
    position: absolute; left: 0; right: 0; bottom: 46px;
    display: flex; align-items: center; justify-content: center; gap: 22px;
    color: var(--text-white); font-size: 17px;
  }
  .back-web .rule { width: 60px; height: 3px; background: var(--brand-red); }

  /* Front side */
  .card-front { top: 720px; background: var(--card-charcoal); }
  .front-band {
    position: absolute; left: 0; right: 0; top: 106px; height: 200px;
    background: var(--brand-blue);
  }
  .front-rule {
    position: absolute; left: 0; right: 0; top: 306px; height: 5px;
    background: var(--brand-red);
  }
  .agent-photo {
    position: absolute; left: 34px; top: 40px; width: 200px; height: 266px;
    background: linear-gradient(170deg, var(--photo-a), var(--photo-b));
  }
  .front-brand {
    position: absolute; left: 300px; top: 52px;
    display: flex; align-items: center; gap: 10px;
    color: var(--text-white); font-size: 26px; font-weight: 600; letter-spacing: 2px;
  }
  .front-brand .mark { width: 10px; height: 10px; background: var(--brand-red); }
  .agent {
    position: absolute; left: 300px; top: 124px; color: var(--text-white);
  }
  .agent-name { font-size: 23px; font-weight: 700; }
  .agent-title { font-size: 15px; color: var(--text-soft); margin-bottom: 10px; }
  .contact-list { list-style: none; }
  .contact-list li {
    display: flex; align-items: center; gap: 10px;
    font-size: 15px; line-height: 23px;
  }
  .contact-list svg { width: 14px; height: 14px; fill: var(--brand-red); flex: none; }
  .front-address {
    position: absolute; left: 40px; bottom: 16px;
    color: var(--text-white); font-size: 17px;
  }
</style>
</head>
<body>

  <section class="card card-back">
    <div class="back-brand">MERIDIAN</div>
    <div class="back-web">
      <span class="rule"></span>
      <span>www.meridianrealestate.com</span>
      <span class="rule"></span>
    </div>
  </section>

  <section class="card card-front">
    <div class="front-band"></div>
    <div class="front-rule"></div>
    <div class="agent-photo" role="img" aria-label="Portrait photo of the agent"></div>

    <div class="front-brand"><span class="mark"></span>Meridian Real Estate</div>

    <div class="agent">
      <div class="agent-name">Diane Marlow</div>
      <div class="agent-title">Managing Director</div>
      <ul class="contact-list">
        <li>
          <svg viewBox="0 0 16 16" aria-hidden="true"><path d="M3 1h3l1 4-2 1a9 9 0 0 0 5 5l1-2 4 1v3a2 2 0 0 1-2 2A13 13 0 0 1 1 3a2 2 0 0 1 2-2z"/></svg>
          555.201.4480
        </li>
        <li>
          <svg viewBox="0 0 16 16" aria-hidden="true"><rect x="4" y="0" width="8" height="16" rx="1.5"/></svg>
          555-310-2291
        </li>
        <li>
          <svg viewBox="0 0 16 16" aria-hidden="true"><path d="M0 3h16v10H0z M1 4l7 5 7-5" stroke="#17255f" stroke-width="1"/></svg>
          dmarlow@meridianrealestate.com
        </li>
        <li>
          <svg viewBox="0 0 16 16" aria-hidden="true"><circle cx="8" cy="8" r="7.5"/><path d="M0.5 8h15M8 0.5v15" stroke="#17255f" stroke-width="1"/></svg>
          www.meridianrealestate.com
        </li>
      </ul>
    </div>

    <div class="front-address">48 Alder Row #2104, Fairview, CO 80000</div>
  </section>

</body>
</html>
```